Meridale Bed Company Needs Business Card

Looking for a very nice looking business card. Creative but not extravagant. We sell beds and pillows across the U.S. and need something professional but catchy. I have attached the logo.

Name : Devin Holt
Title : President
Phone : (800) 471-2960
Email: sleep@quilmora.com
Website: www.quilmora.com

Can be single-sided or double-sided
horizontal or vertical

Can use Blues/Greys

Target Market(s)

Mass Market

Industry/Entity Type

Retail

Contact Information for Business Card

Name : Devin Holt
Title : President
Phone : (800) 471-2960
Email: sleep@quilmora.com
Website: www.quilmora.com

Requirements
Must have
• Clean, Modern, Smooth
• Can use Blues/Greys
• On the other side without the information - have something simple like www.quilmora.com or our logo
Nice to have
• Surprise me
Should not have
• Nothing crazy, nothing cluttered

```html
<!DOCTYPE html>
<html lang="en">
<head>
<meta charset="utf-8">
<title>Quilmora Business Card</title>
<link rel="stylesheet" href="https://fonts.googleapis.com/css2?family=Figtree:wght@300;400&display=swap">
<style>
  :root {
    --backdrop: #dfe3e3;
    --brand-blue: #4bd0f5;
    --card-white: #ffffff;
    --ink: #333a3d;
    --shadow: rgba(60, 70, 72, 0.28);
  }
  * { margin: 0; padding: 0; box-sizing: border-box; }
  html, body {
    width: 1200px;
    height: 759px;
    overflow: hidden;
    background: var(--backdrop);
    font-family: "Figtree", sans-serif;
  }
  .canvas {
    position: relative;
    width: 1200px;
    height: 759px;
  }
  .card {
    position: absolute;
    width: 398px;
    height: 229px;
    box-shadow: 6px 6px 8px var(--shadow);
    text-align: center;
  }
  .card--front {
    left: 158px;
    top: 270px;
    background: var(--brand-blue);
  }
  .card--back {
    left: 621px;
    top: 271px;
    background: var(--card-white);
  }
  .wordmark {
    font-weight: 300;
    letter-spacing: 1px;
    line-height: 1;
  }
  .card--front .wordmark {
    color: var(--card-white);
    font-size: 50px;
    margin-top: 80px;
  }
  .card--back .wordmark {
    color: var(--brand-blue);
    font-size: 47px;
    margin-top: 24px;
  }
  .holder-name {
    color: var(--brand-blue);
    font-size: 15px;
    font-weight: 400;
    margin-top: 21px;
    letter-spacing: 0.3px;
  }
  .holder-title {
    color: var(--ink);
    font-size: 11px;
    margin-top: 2px;
  }
  .contact {
    list-style: none;
    margin-top: 25px;
    color: var(--ink);
    font-size: 11.5px;
    line-height: 16px;
  }
</style>
</head>
<body>
  <main class="canvas">
    <section class="card card--front" aria-label="Card front">
      <p class="wordmark">quilmora</p>
    </section>
    <section class="card card--back" aria-label="Card back">
      <p class="wordmark">quilmora</p>
      <h1 class="holder-name">Devin Holt</h1>
      <p class="holder-title">President</p>
      <ul class="contact">
        <li>(800) 471-2960</li>
        <li>sleep@quilmora.com</li>
        <li>www.quilmora.com</li>
      </ul>
    </section>
  </main>
</body>
</html>
```